Photographer's price list

I am a photographer who runs a studio (Marrowfield Studio) and need to have a document to send clients detailing my packages (collections) and prices. I have written the text in a word document and need a designer to lay it out for me using my logo and two specific fonts: DejaVu Sans and LainieDaySH.

The look should be clean and modern and keep in the same style as my logo. I will primarily be using the final product as a PDF file to email to potential clients. It should stay black and white.

I would also like to be able to update the text myself as my prices and packages change. So I would like a PSD file.

I think I would like for the document to be in landscape format with "Collections" on one side and A la Carte on the other, but I am open to other ideas.

As for sizing, it should be a standard size so that clients can print it out if they like.

Industry/Entity Type

Landscape

Requirements
Must have
• my logo
fonts: DejaVu and LainieDaySH
Easy to email
Easy to display on one page upon opening
Standard size so that printing from a home computer is easy to do.

```html
<!DOCTYPE html>
<html lang="en">
<head>
<meta charset="utf-8">
<title>Marrowfield Studio – 2013 Photography Collections</title>
<link rel="stylesheet" href="https://fonts.googleapis.com/css2?family=Didact+Gothic&family=Open+Sans:wght@400;600&family=Oswald:wght@600&family=PT+Sans+Narrow&display=swap">
<style>
  :root {
    --ink: #231f20;
    --paper: #ffffff;
    --mist: #e3e4e6;
    --ring: #c9c9cb;
    --soft: #8a8a8c;
    --pale: #d8d8d8;
    --stage: #3a3a3a;
  }
  * { margin: 0; padding: 0; box-sizing: border-box; }
  html, body { width: 1200px; height: 855px; overflow: hidden; background: var(--stage); }
  .sheet { position: relative; width: 1200px; height: 855px; }
  .page { position: absolute; width: 533px; height: 376px; overflow: hidden; }
  .page--back { left: 67px; top: 20px; background: var(--paper); }
  .page--front { left: 600px; top: 20px; background: var(--ink); }
  .page--collections { left: 67px; top: 436px; background: var(--mist); }
  .page--carte { left: 600px; top: 436px; background: var(--ink); }

  .brand {
    position: absolute; border-radius: 50%; background: var(--paper);
    border: 9px solid var(--ring); display: flex; align-items: center; justify-content: center;
    font-family: "Didact Gothic", sans-serif; color: var(--ink); letter-spacing: 2px;
  }

  /* back */
  .back__band { position: absolute; left: 0; top: 131px; width: 100%; height: 111px; background: var(--ink); }
  .page--back .brand { left: 26px; top: 111px; width: 146px; height: 146px; font-size: 13px; }
  .about { position: absolute; left: 203px; top: 142px; width: 205px; color: var(--paper); font-family: "Open Sans", sans-serif; }
  .about h2 { font-weight: 400; font-size: 11px; margin-bottom: 6px; }
  .about p { font-size: 5.6px; line-height: 1.35; margin-bottom: 4px; }
  .web { position: absolute; left: 35px; top: 263px; font-family: "Didact Gothic", sans-serif; font-size: 8px; letter-spacing: 2px; color: var(--ink); }

  /* front */
  .front__strip { position: absolute; left: 0; top: 0; width: 100%; height: 10px; background: var(--ring); }
  .front__photo { position: absolute; left: 0; top: 11px; width: 368px; height: 255px; background: linear-gradient(135deg, #f2f2f2, #9a9a9a 55%, #3c3c3c); }
  .page--front .brand { left: 383px; top: 91px; width: 126px; height: 126px; font-size: 11px; border-width: 7px; }
  .front__year { position: absolute; right: 30px; top: 236px; font-family: "Oswald", sans-serif; font-weight: 600; font-size: 52px; color: var(--paper); line-height: 1; }
  .front__title { position: absolute; left: 16px; top: 298px; font-family: "Oswald", sans-serif; font-weight: 600; font-size: 41px; color: var(--paper); letter-spacing: 0.5px; line-height: 1; }

  /* inside 1 */
  .inc { position: absolute; left: 23px; top: 42px; width: 495px; font-family: "Didact Gothic", sans-serif; color: var(--ink); }
  .inc h2 { font-weight: 400; font-size: 22px; margin-bottom: 10px; }
  .inc p { font-size: 6.6px; line-height: 2.1; color: var(--soft); }
  .coll { position: absolute; width: 230px; font-family: "Didact Gothic", sans-serif; }
  .coll h3 { font-weight: 400; font-size: 22px; color: var(--ink); margin-bottom: 4px; }
  .coll p { font-family: "PT Sans Narrow", sans-serif; font-size: 6.5px; line-height: 1.45; color: var(--soft); margin-bottom: 4px; }
  .bubbles { position: absolute; left: 0; width: 100%; }
  .page--collections .bubbles { top: 310px; height: 66px; background: linear-gradient(180deg, var(--mist), #cfd0d2 50%, var(--mist)); }
  .page--carte .bubbles { height: 68px; background: linear-gradient(180deg, var(--ink), #3e3b3c 50%, var(--ink)); }

  /* inside 2 */
  .item { position: absolute; width: 218px; color: var(--pale); }
  .item h3 { font-family: "Didact Gothic", sans-serif; font-weight: 400; font-size: 11px; line-height: 1.25; margin-bottom: 4px; }
  .item h3 span { margin-left: 14px; }
  .item p { font-family: "PT Sans Narrow", sans-serif; font-size: 6.4px; line-height: 1.45; color: var(--paper); }
</style>
</head>
<body>
<main class="sheet">

  <section class="page page--back">
    <div class="back__band"></div>
    <div class="brand">MARROWFIELD</div>
    <div class="about">
      <h2>About us</h2>
      <p>Marrowfield Studio, based in Frankfurt, Germany, is a newly launched studio led by photographer Clara Dunmore Hale. She specializes in portrait, children and cause-related photography, and is currently working on a collection featuring mothers and children.</p>
      <p>Clara holds a Master's in Foreign Service and International Development from Harlow Institute, and a BA from Wrenford College. She is available for assignments worldwide.</p>
    </div>
    <div class="web">www.marrowfieldstudio.com</div>
  </section>

  <section class="page page--front">
    <div class="front__strip"></div>
    <div class="front__photo" role="img" aria-label="Black and white portrait photograph of three children embracing"></div>
    <div class="brand">MARROWFIELD</div>
    <div class="front__year">2013</div>
    <h1 class="front__title">PHOTOGRAPHY COLLECTIONS</h1>
  </section>

  <section class="page page--collections">
    <div class="inc">
      <h2>All collections&nbsp; include:</h2>
      <p>One to two hour portrait session with photographer in location of your choice<br>(unlimited time if necessary!)<br>
      Clara will create a presentation video with hand-selected music and custom editing, which tells your story, highlights the best images, and reveals the connections within your family. An online gallery for viewing and ordering helps you share your images with family and friends.</p>
    </div>
    <div class="coll" style="left:23px;top:146px">
      <h3>Collection 1: 300 €</h3>
      <p>Your favorite five images from the session will be professionally edited and presented to you on disk as high resolution jpegs</p>
    </div>
    <div class="coll" style="left:269px;top:146px">
      <h3>Collection 3: 500 €</h3>
      <p>Your favorite fifteen images from the session will be professionally edited and presented to you on disk as high resolution jpegs<br>Your favorite two images from the session will be professionally printed for you (20x30cm) on Velmont paper, Clara's favorite for portraits.</p>
    </div>
    <div class="coll" style="left:23px;top:223px">
      <h3>Collection 2: 400 €</h3>
      <p>Your favorite ten images from the session will be professionally edited and given to you on disk as high resolution jpegs<br>Your favorite image from the session will be professionally printed for you (20x30cm) on Velmont paper, Clara's favorite for portraits.</p>
    </div>
    <div class="coll" style="left:269px;top:223px">
      <h3>Collection 4: 600 €</h3>
      <p>ALL presented images from the session will be professionally edited and presented to you on disk as high resolution jpegs (approximately 40+ images)</p>
      <p>Your favorite two images from the session will be professionally printed for you (20x30cm) on Velmont paper, Clara's favorite for portraits.</p>
    </div>
    <div class="bubbles" role="img" aria-label="Decorative pattern of soft grey bubbles"></div>
  </section>

  <section class="page page--carte">
    <div class="bubbles" style="top:0" role="img" aria-label="Decorative pattern of soft grey bubbles"></div>
    <div class="item" style="left:28px;top:88px">
      <h3>A LA CARTE</h3>
      <p>These products may be purchased separately to complement your collection. A consultation with Clara will help you decide which products are best for gifts and for your home.</p>
    </div>
    <div class="item" style="left:28px;top:158px">
      <h3>A LA CARTE - 25 € EACH<br>HIGH RESOLUTION DIGITAL IMAGES</h3>
      <p>Perfect if you just need to add "one more image" to your collection!<br>High-resolution jpeg file</p>
    </div>
    <div class="item" style="left:28px;top:231px">
      <h3>A LA CARTE - 25 €<span>MATT PRINTS</span></h3>
      <p>Each print is professionally edited, printed on archival photo paper.<br>Purchase includes the JPEG file for your personal digital use.<br>20x30 cm and Smaller</p>
    </div>
    <div class="item" style="left:266px;top:74px">
      <h3>A LA CARTE - 45 €<span>VELMONT PRINTS</span></h3>
      <p>Prints on Velmont (watercolor) paper are Clara's favorite for large format color prints 30x40 cm</p>
    </div>
    <div class="item" style="left:266px;top:123px">
      <h3>A LA CARTE - 100 €<span>CANVAS PRINTS</span></h3>
      <p>Ready-to-hang, stretched canvas wall art of your favorite images<br>30x40 cm</p>
    </div>
    <div class="item" style="left:266px;top:175px">
      <h3>A LA CARTE - 350 €<span>FRAMED + MATTED PRINTS</span></h3>
      <p>Beautiful Velmont prints finished with wide mats and simple, elegant frames of your choice 30x40 inch</p>
    </div>
    <div class="item" style="left:266px;top:231px">
      <h3>PRICES BEGIN AT - 100 €<br>CUSTOM DESIGNED ALBUMS</h3>
      <p>Images from your session are selected for the custom design of an album and bound in a book for a modern presentation of your images. There are a number of cover choices for the classic flush-mount and beautifully crafted albums. A great way to display all of your favorite images from your session on your coffee table.</p>
    </div>
    <div class="bubbles" style="top:308px" role="img" aria-label="Decorative pattern of soft grey bubbles"></div>
  </section>

</main>
</body>
</html>
```